real esate business card with company logo and name

we need a business card design for a real esate company

The company name is Walsh & Brand Pty Ltd, and we have our logo designed and will upload. We want classic or moden feel. Black or white background. looks more textured. Should include folowinginformations
Owen Walsh and Lucy Brand
Sales Agents & Onsite Manager
p: 07 5948 2063
F: 07 5948 2174
M:0431 857 219
3/42 Marlow Crescent, FERNLEA QLD 4213

We want this business card looks professonal. Thank you in advance.

Industry/Entity Type

Real Estate Agent

Contact Information for Business Card

Owen Walsh and Lucy Brand
Onsite Manager & Sales Agents
p: 07 5948 2063
M:0431 857 219

Font styles to use
Serif

Colors
000000
fbfbfb
333333
959595

Requirements
Must have
• company logo and name, black or white back ground

```html
<!DOCTYPE html>
<html lang="en">
<head>
<meta charset="utf-8">
<title>Walsh &amp; Brand Pty Ltd — Business Card</title>
<link rel="stylesheet" href="https://fonts.googleapis.com/css2?family=Lato:wght@400;700&display=swap">
<style>
  :root {
    --backdrop: #3a3a3a;
    --ink: #000000;
    --paper: #ebebed;
    --strip: #d4d4d6;
    --text-light: #e6e6e6;
    --brand-grey: #959595;
  }
  * { margin: 0; padding: 0; box-sizing: border-box; }
  html, body {
    width: 1200px; height: 1086px; overflow: hidden;
    background: var(--backdrop);
    font-family: "Lato", sans-serif;
  }
  .canvas { position: relative; width: 1200px; height: 1086px; }

  .card {
    position: absolute; left: 254px; width: 678px;
    box-shadow: 0 4px 10px rgba(0,0,0,.45);
    overflow: hidden;
  }

  /* Front */
  .card--front { top: 126px; height: 388px; background: var(--ink); }
  .front__strip {
    position: absolute; left: 0; top: 0; width: 32px; height: 100%;
    background: var(--strip);
  }
  .front__strip svg { position: absolute; left: 0; top: 140px; }
  .agent { position: absolute; left: 47px; top: 56px; color: var(--text-light); }
  .agent__name { font-weight: 700; font-size: 27px; line-height: 1.1; }
  .agent__role { font-size: 20px; line-height: 1.3; }
  .contact-list {
    position: absolute; left: 48px; top: 188px; list-style: none;
    color: var(--text-light); font-size: 19px; line-height: 23.5px;
  }
  .contact-list li { display: flex; align-items: center; gap: 7px; }
  .contact-list svg { width: 13px; height: 13px; fill: var(--text-light); flex: none; }
  .address {
    position: absolute; left: 46px; top: 275px;
    color: var(--text-light); font-size: 17px; line-height: 21.5px; font-style: normal;
  }
  .brand {
    position: absolute; display: flex; flex-direction: column; align-items: center;
    color: var(--brand-grey); font-weight: 400; letter-spacing: .5px; white-space: nowrap;
  }
  .brand__mark { background: var(--brand-grey); }
  .card--front .brand { left: 545px; top: 120px; transform: translateX(-50%); gap: 22px; font-size: 18px; }
  .card--front .brand__mark { width: 100px; height: 100px; }

  /* Back */
  .card--back { top: 587px; height: 385px; background: var(--paper); }
  .back__band {
    position: absolute; left: 0; top: 105px; width: 100%; height: 181px;
    background: var(--ink);
  }
  .card--back .brand { left: 50%; top: 34px; transform: translateX(-50%); gap: 18px; font-size: 12px; }
  .card--back .brand__mark { width: 62px; height: 62px; }
</style>
</head>
<body>
<main class="canvas">
  <section class="card card--front" aria-label="Card front">
    <div class="front__strip">
      <svg width="32" height="40" viewBox="0 0 32 40"><line x1="0" y1="32" x2="32" y2="0" stroke="#000" stroke-width="1.5"/></svg>
    </div>
    <div class="agent">
      <h1 class="agent__name">Owen Walsh</h1>
      <p class="agent__role">Sales Agents</p>
    </div>
    <ul class="contact-list">
      <li><svg viewBox="0 0 16 16"><path d="M4 0h8a1 1 0 0 1 1 1v14a1 1 0 0 1-1 1H4a1 1 0 0 1-1-1V1a1 1 0 0 1 1-1zm0 2v10h8V2zm4 11a1 1 0 1 0 0 2 1 1 0 0 0 0-2z"/></svg>0431 857 219</li>
      <li><svg viewBox="0 0 16 16"><path d="M1 5c2-3 12-3 14 0v2h-3V5.5h-8V7H1zm2 3h10l2 6H1zm5 1.5a2 2 0 1 0 0 4 2 2 0 0 0 0-4z"/></svg>07 5948 2063</li>
      <li><svg viewBox="0 0 16 16"><path d="M4 1h8v4H4zM1 6h14v6h-3v3H4v-3H1zm4 4v4h6v-4z"/></svg>07 5948 2174</li>
    </ul>
    <address class="address">3/42 Marlow Crescent<br>FERNLEA QLD 4213</address>
    <div class="brand">
      <span class="brand__mark" aria-hidden="true"></span>
      <span class="brand__name">WALSH &amp; BRAND PTY LTD.</span>
    </div>
  </section>

  <section class="card card--back" aria-label="Card back">
    <div class="back__band">
      <div class="brand">
        <span class="brand__mark" aria-hidden="true"></span>
        <span class="brand__name">WALSH &amp; BRAND PTY LTD.</span>
      </div>
    </div>
  </section>
</main>
</body>
</html>
```